BOLD & MINIMALIST DESIGN NEEDED

We want a very bold but minimalistic business card design that is impactful and utilizes both sides of the business card. Our current logo is included for your use.

We want bold fonts and good use of negative space. We don't want the logo to overpower the design.

Target Market(s)

Professionals who are building new commercial buildings.

Industry/Entity Type

Construction

Contact Information for Business Card

Name, Title, email, office phone, cell phone, website

Font styles to use
Serif
Sans Serif

Requirements
Must have
• Bold design!

```html
<!DOCTYPE html>
<html lang="en">
<head>
<meta charset="utf-8">
<title>Ridgeline Design + Build – Business Card</title>
<link rel="stylesheet" href="https://fonts.googleapis.com/css2?family=Poppins:wght@400;500;600;700&display=swap">
<style>
  :root {
    --page-bg: #2a2a2a;
    --card-bg: #252525;
    --card-bg-light: #2c2c2c;
    --text-white: #f2f2f2;
    --text-soft: #d6d6d6;
    --brand-green: #7cc242;
  }
  * { box-sizing: border-box; margin: 0; padding: 0; }
  html, body {
    width: 1200px;
    height: 576px;
    overflow: hidden;
    background: var(--page-bg);
    font-family: "Poppins", sans-serif;
  }
  .stage {
    position: relative;
    width: 1200px;
    height: 576px;
  }
  .card {
    position: absolute;
    top: 139px;
    height: 293px;
    border-radius: 8px;
    background: linear-gradient(160deg, var(--card-bg-light), var(--card-bg));
  }
  .card--front { left: 102px; width: 485px; }
  .card--back  { left: 597px; width: 480px; }

  .front-brand {
    position: absolute;
    left: 48px;
    top: 118px;
    color: var(--text-white);
    font-weight: 700;
    font-size: 26px;
    line-height: 1.05;
    letter-spacing: 0.5px;
    text-transform: uppercase;
  }
  .front-brand span {
    display: block;
    font-size: 14px;
    letter-spacing: 4px;
  }

  .back-brand {
    position: absolute;
    left: 52px;
    top: 118px;
    display: flex;
    align-items: center;
    gap: 10px;
  }
  .back-brand__mark {
    width: 22px;
    height: 22px;
    background: var(--brand-green);
  }
  .back-brand__name {
    color: var(--text-white);
    font-weight: 700;
    font-size: 19px;
    line-height: 1.1;
    text-transform: uppercase;
    letter-spacing: 0.5px;
  }

  .contact {
    position: absolute;
    left: 265px;
    top: 86px;
  }
  .contact__name {
    color: var(--brand-green);
    font-weight: 500;
    font-size: 19px;
    line-height: 1.2;
  }
  .contact__title {
    color: var(--text-soft);
    font-size: 11.5px;
    margin-top: 1px;
  }
  .contact__list {
    list-style: none;
    margin-top: 24px;
  }
  .contact__item {
    display: flex;
    align-items: center;
    gap: 9px;
    color: var(--text-soft);
    font-size: 12px;
    line-height: 17px;
  }
  .contact__icon { width: 10px; height: 10px; fill: var(--brand-green); flex: none; }
</style>
</head>
<body>
<main class="stage">
  <section class="card card--front" aria-label="Card front">
    <div class="front-brand">Ridgeline<span>Design + Build</span></div>
  </section>

  <section class="card card--back" aria-label="Card back">
    <div class="back-brand">
      <div class="back-brand__mark"></div>
      <div class="back-brand__name">Ridgeline<br>Design + Build</div>
    </div>
    <div class="contact">
      <p class="contact__name">Daniel Reyes</p>
      <p class="contact__title">Director</p>
      <ul class="contact__list">
        <li class="contact__item">
          <svg class="contact__icon" viewBox="0 0 10 10" aria-hidden="true"><path d="M1 3c0-1.5 1.5-2 4-2s4 .5 4 2v1H7V3H3v1H1z"/><path d="M2 5h6l1 4H1z"/></svg>
          555-014-0127
        </li>
        <li class="contact__item">
          <svg class="contact__icon" viewBox="0 0 10 10" aria-hidden="true"><path d="M0 2h10v6H0z"/><path d="M0 2l5 3.5L10 2" fill="none" stroke="#252525" stroke-width="1"/></svg>
          dan@ridgelinebuild.com
        </li>
        <li class="contact__item">
          <svg class="contact__icon" viewBox="0 0 10 10" aria-hidden="true"><circle cx="5" cy="5" r="4.5"/><path d="M0.5 5h9M5 0.5v9M2 2.5q3 1.5 6 0M2 7.5q3-1.5 6 0" fill="none" stroke="#252525" stroke-width="0.7"/></svg>
          www.ridgelinebuild.com
        </li>
      </ul>
    </div>
  </section>
</main>
</body>
</html>
```